Animal Eye Clinic needs a Business card

We are a new veterinary ophthalmology practice (Ridgeline Pet Vision Care) and we need a business card designed. We only see animal eyes - we are not a regular veterinary clinic. We already have a logo. We are looking for a professional, good looking business card to hand out to our clients. We are looking for something simple but professional and contemporary. Our logo is likely the only picture/graphic that needs to be on the card.
Updates

Contact Information for Business Card

Delia Vossman, BSc, DVM, MSc, DipACVO
Veterinary Ophthalmologist

Phone: 250.418.3927
Email: ridgelinepetvisioncare@mailbox-example.net
Website: ridgelinepetvisioncare-example.net
Address: 1874 Thornbury Rd
Kelowna, BC, V1X 4M9

Colors

Designer to choose colors to be used in the design.

Requirements
Must have
• Our logo (attached)

```html
<!DOCTYPE html>
<html lang="en">
<head>
<meta charset="utf-8">
<title>Ridgeline Pet Vision Care – Business Card</title>
<link href="https://fonts.googleapis.com/css2?family=Arimo:wght@400;700&family=Fira+Sans+Condensed:wght@600&display=swap" rel="stylesheet">
<style>
  :root {
    --teal: #0f9aa8;
    --teal-faint: #24a6b2;
    --teal-wash: #eaf6f7;
    --white: #ffffff;
    --ink-grey: #6d6f71;
    --backdrop: #e9e9e9;
  }
  html, body {
    margin: 0;
    padding: 0;
    width: 1125px;
    height: 1200px;
    overflow: hidden;
    background: var(--backdrop);
  }
  .canvas {
    position: relative;
    width: 1125px;
    height: 1200px;
    font-family: "Arimo", Arial, sans-serif;
  }
  .card {
    position: absolute;
    left: 162px;
    width: 766px;
    height: 436px;
    overflow: hidden;
    box-shadow: 0 2px 4px rgba(0,0,0,0.25);
  }
  .card-front {
    top: 112px;
    background: var(--teal);
    border-radius: 218px 0 0 218px;
    color: var(--white);
  }
  .card-back {
    top: 628px;
    background: var(--white);
    border-radius: 0 218px 218px 0;
  }
  .decor-circle {
    position: absolute;
    border-radius: 50%;
  }
  .card-front .decor-circle {
    left: 22px;
    top: 40px;
    width: 356px;
    height: 356px;
    background: var(--teal-faint);
  }
  .card-back .decor-circle {
    left: 398px;
    top: 30px;
    width: 370px;
    height: 370px;
    background: var(--teal-wash);
  }
  .contact {
    position: absolute;
    left: 405px;
    top: 124px;
  }
  .contact-name {
    margin: 0;
    font-family: "Fira Sans Condensed", "Arial Narrow", sans-serif;
    font-weight: 600;
    font-size: 20px;
    letter-spacing: 0.3px;
    text-transform: uppercase;
  }
  .contact-name .credentials {
    font-size: 14px;
    text-transform: none;
  }
  .contact-role {
    margin: 4px 0 0;
    font-size: 16px;
  }
  .contact-address {
    margin: 22px 0 0;
    font-size: 17px;
    line-height: 22px;
    font-style: normal;
  }
  .contact-lines {
    list-style: none;
    margin: 10px 0 0;
    padding: 0;
    font-size: 15px;
    line-height: 23px;
  }
  .contact-lines li {
    display: flex;
    align-items: center;
  }
  .contact-lines svg {
    width: 13px;
    height: 13px;
    margin-right: 12px;
    fill: var(--white);
    flex: none;
  }
  .brand {
    position: absolute;
    left: 95px;
    top: 180px;
    display: flex;
    align-items: center;
  }
  .brand-dot {
    width: 62px;
    height: 62px;
    border-radius: 50%;
    background: var(--teal);
    margin-right: 22px;
  }
  .brand-name {
    font-family: "Arimo", Arial, sans-serif;
    font-weight: 700;
    font-size: 34px;
    color: var(--teal);
    letter-spacing: 0.2px;
  }
</style>
</head>
<body>
<main class="canvas">
  <section class="card card-front" aria-label="Business card front">
    <div class="decor-circle" aria-hidden="true"></div>
    <div class="contact">
      <h1 class="contact-name">Delia Vossman, <span class="credentials">BSc, DVM, MSc, DipACVO</span></h1>
      <p class="contact-role">Veterinary Ophthalmologist</p>
      <address class="contact-address">1874 Thornbury Rd<br>Kelowna, BC, V1X 4M9</address>
      <ul class="contact-lines">
        <li>
          <svg viewBox="0 0 16 16" aria-hidden="true"><path d="M3.5 1l2.5 3-1.5 1.8c.8 1.9 2.3 3.4 4.2 4.2L10.5 8.5l3 2.5-1.2 2.8C7 14 2 9 2.2 2.2z"/></svg>
          250.418.3927
        </li>
        <li>
          <svg viewBox="0 0 16 16" aria-hidden="true"><path d="M1 3h14v1.2L8 8.8 1 4.2zM1 5.6l7 4.6 7-4.6V13H1z"/></svg>
          ridgelinepetvisioncare@mailbox-example.net
        </li>
        <li>
          <svg viewBox="0 0 16 16" aria-hidden="true"><circle cx="8" cy="8" r="7"/><path d="M4 5c2 0 2 2 4 2s1 3 3 3M9 2c-1 2 1 3 0 5" stroke="#0f9aa8" stroke-width="1.3" fill="none"/></svg>
          ridgelinepetvisioncare-example.net
        </li>
      </ul>
    </div>
  </section>

  <section class="card card-back" aria-label="Business card back">
    <div class="decor-circle" aria-hidden="true"></div>
    <div class="brand">
      <span class="brand-dot" aria-hidden="true"></span>
      <span class="brand-name">Ridgeline Pet Vision Care</span>
    </div>
  </section>
</main>
</body>
</html>
```